I need a business card design for a real estate finance, development and management business. We deal with high net worth clients and ask that the business card be neat, clean and sophisticated. We like the attached logo design, font and color and want to incorporate all this into the business card.

Industry/Entity Type

Real Estate

```html
<!DOCTYPE html>
<html lang="en">
<head>
<meta charset="utf-8">
<title>Silver Harbor business card</title>
<link rel="stylesheet" href="https://fonts.googleapis.com/css2?family=Open+Sans:ital,wght@0,400;0,600;0,700;1,400&display=swap">
<style>
  :root {
    --brand-blue: #2161a3;
    --ink: #111418;
    --paper: #ffffff;
    --backdrop: #e4e5e7;
  }
  * { margin: 0; padding: 0; box-sizing: border-box; }
  html, body { width: 1200px; height: 947px; overflow: hidden; }
  body {
    background: var(--backdrop);
    font-family: "Open Sans", Arial, sans-serif;
    position: relative;
  }
  .card {
    position: absolute;
    width: 560px;
    height: 320px;
    background: var(--paper);
    overflow: hidden;
    box-shadow: 0 6px 18px rgba(0,0,0,0.12);
  }
  .card--front { left: 580px; top: 110px; }
  .card--back { left: 60px; top: 500px; }
  .card__swoosh { position: absolute; inset: 0; width: 100%; height: 100%; }

  .wordmark {
    position: absolute;
    color: var(--brand-blue);
    font-weight: 600;
    letter-spacing: 0.08em;
    white-space: nowrap;
  }
  .card--front .wordmark { left: 0; right: 0; top: 118px; text-align: center; font-size: 40px; }
  .card--back .wordmark { left: 300px; top: 58px; font-size: 22px; }

  .person { position: absolute; left: 38px; top: 104px; color: var(--brand-blue); }
  .person__name { font-size: 22px; font-weight: 400; letter-spacing: 0.02em; }
  .person__name strong { font-weight: 700; }
  .person__role { font-size: 15px; font-style: italic; margin-top: 2px; }

  .divider {
    position: absolute;
    left: 262px; top: 112px;
    width: 2px; height: 130px;
    background: var(--brand-blue);
  }

  .contact {
    position: absolute;
    left: 290px; top: 112px;
    list-style: none;
    color: var(--ink);
    font-size: 15px;
    line-height: 1.3;
  }
  .contact li { display: flex; align-items: flex-start; gap: 10px; margin-bottom: 6px; }
  .contact svg { width: 14px; height: 14px; flex: none; margin-top: 3px; fill: var(--ink); }
</style>
</head>
<body>

<section class="card card--front" aria-label="Card front">
  <svg class="card__swoosh" viewBox="0 0 560 320" preserveAspectRatio="none" aria-hidden="true">
    <path d="M0 0 H560 V5 C380 10 160 30 0 58 Z" fill="var(--brand-blue)"/>
    <path d="M0 246 C180 258 380 284 560 296 V320 H0 Z" fill="var(--ink)"/>
    <path d="M0 262 C200 282 400 302 560 306 V320 H0 Z" fill="var(--brand-blue)"/>
  </svg>
  <div class="wordmark">SILVER HARBOR</div>
</section>

<section class="card card--back" aria-label="Card back">
  <svg class="card__swoosh" viewBox="0 0 560 320" preserveAspectRatio="none" aria-hidden="true">
    <path d="M0 0 H560 V5 C380 10 160 30 0 58 Z" fill="var(--brand-blue)"/>
    <path d="M0 246 C180 258 380 284 560 296 V320 H0 Z" fill="var(--ink)"/>
    <path d="M0 262 C200 282 400 302 560 306 V320 H0 Z" fill="var(--brand-blue)"/>
  </svg>

  <div class="wordmark">SILVER HARBOR</div>

  <div class="person">
    <div class="person__name">YOUR<strong>NAME</strong></div>
    <div class="person__role">your designation</div>
  </div>

  <div class="divider"></div>

  <ul class="contact">
    <li>
      <svg viewBox="0 0 14 14" aria-hidden="true"><path d="M7 0a5 5 0 0 0-5 5c0 3.5 5 9 5 9s5-5.5 5-9a5 5 0 0 0-5-5zm0 7a2 2 0 1 1 0-4 2 2 0 0 1 0 4z"/></svg>
      <span>Your Local or business<br>address.</span>
    </li>
    <li>
      <svg viewBox="0 0 14 14" aria-hidden="true"><path d="M3 1l2.5 3-1.5 1.5c.8 1.8 2.2 3.2 4 4L9.5 8 13 10.5 11.5 13C6 13 1 8 1 2.5z"/></svg>
      <span>+000 1234 5679</span>
    </li>
    <li>
      <svg viewBox="0 0 14 14" aria-hidden="true"><path d="M0 3h14v9H0z M1 4l6 4.5L13 4" fill="var(--ink)"/><path d="M1 4l6 4.5L13 4" fill="none" stroke="#fff" stroke-width="1"/></svg>
      <span>+000 1234 5679</span>
    </li>
    <li>
      <svg viewBox="0 0 14 14" aria-hidden="true"><path d="M0 3h14v9H0z"/><path d="M1 4l6 4.5L13 4" fill="none" stroke="#fff" stroke-width="1.2"/></svg>
      <span>name@yourwebsite.com</span>
    </li>
    <li>
      <svg viewBox="0 0 14 14" aria-hidden="true"><circle cx="7" cy="7" r="6.5"/><path d="M0.5 7h13M7 0.5v13M2 3.5h10M2 10.5h10" stroke="#fff" stroke-width="0.9" fill="none"/><ellipse cx="7" cy="7" rx="3" ry="6.5" fill="none" stroke="#fff" stroke-width="0.9"/></svg>
      <span>www.yourwebsite.com</span>
    </li>
  </ul>
</section>

</body>
</html>
```